Bluefern Business Services needs a new interactive and interesting website

We need an interesting, professional, modern and functional company website for Bluefern Business Services - a young IT Services company based out of Chennai, India.

Bluefern Business Services is a fully owned subsidiary of Marlow Goods, one of the world's leading direct to consumer wine merchant.

We already have a registered company logo which must feature in the website.

We conceive, design, develop, test, implement and support IT solutions across the entire Marlow Goods IT landscape. For ex : We currently run about 25 e-commerce websites for Marlow Goods on ATG and Dot Net.

We would like to see our corporate colors used in the website. (Burgundy wine and wine green - source: www.bluefernbs-site.com)

We are looking at this website to communicate a fun, friendly and professionally managed company - reaching out to career seekers, prospective customers and general public.

For reference - The company name 'Bluefern' is an inspiration from the Marlow Goods lineage.

The second image with the world map is stickered on our main entrance to the office, I am not sure where this can be used -just putting it out there..

Please note that there are only a few more days to submit designs for this contest  !

I would appreciate if you can help posting your designs in time for our review and consideration.

Thanks.

Reason: Thanks for your inputs. We have a number of designers and a lot to digest and work with in the past few days. There has been a rush of new designs in the last few days Hence we will require more time to process these and make our decision. Hence i am requesting the contest to be open for more days. Regards, Tarun

Target Market(s)

Prospective job seekers who want to know more about the company and also wish to apply for a job vacancy
People wanting to know more about the company in general and our progress
People who want to see what we offer and how we can help them too - prospective customers
Companies that are interested in our IT Captive journey and are looking for a business opportunity

Industry/Entity Type

E-Commerce

Requirements
Must have
• Log In/ Register facility acting as a Single Sign on for Intranet (Employees)

Facility to post job vacancies (with an expiry date) and enable people to apply for a role and upload their CV/Resume.

Facility to Review Job applications

Facility for website visitors to contact Bluefern business Services via an online 'Contact Us' form with a split of job seekers and business opportunities

Gallery facility to upload pictures regarding company events
Nice to have
• Less Cluttered and contemporary design
Some Wine/Vineyard inspirations will be good but not too much, the company is an IT services company

```html
<!DOCTYPE html>
<html lang="en">
<head>
<meta charset="utf-8">
<title>Bluefern Business Services</title>
<link href="https://fonts.googleapis.com/css2?family=Ubuntu:wght@300;400;500&family=Ubuntu+Condensed&family=Open+Sans:wght@300;400;600&family=Arimo:wght@400;700&display=swap" rel="stylesheet">
<style>
:root{
  --burgundy:#7a0a3c;
  --burgundy-dark:#5a0028;
  --magenta:#a4135a;
  --wine-green:#7d8a2a;
  --green-text:#8a9430;
  --ink:#222;
  --body:#555;
  --muted:#999;
  --rule:#dcdcdc;
  --nav-bg:#ececec;
  --footer-bg:#e9e9e9;
}
*{margin:0;padding:0;box-sizing:border-box}
html,body{width:1016px;height:1200px;overflow:hidden}
body{position:relative;background:#fff;font-family:"Open Sans",sans-serif;color:var(--body)}
.abs{position:absolute}
.header-band{left:0;top:0;width:1016px;height:391px;background:linear-gradient(90deg,#8a0c48 0%,#a4135a 45%,#7d0a3e 100%)}
.header-photo{left:620px;top:0;width:396px;height:120px;background:radial-gradient(ellipse at 70% 40%,#3b4a6a 0%,#2a2f3e 45%,rgba(122,10,60,0) 80%)}
.vineyard-bg{left:0;top:458px;width:1016px;height:640px;background:linear-gradient(90deg,#5d6a2e 0%,#b8b08a 4%,#fff 7%,#fff 93%,#b8b08a 96%,#5d6a2e 100%),linear-gradient(180deg,#fff 0%,#8a8a50 100%);background-blend-mode:multiply}
.logo{left:84px;top:22px;color:#fff;font-family:"Ubuntu",sans-serif}
.logo-mark{display:inline-block;width:26px;height:26px;border-radius:50%;background:#fff;vertical-align:middle;margin-right:6px}
.logo-name{font-size:38px;font-weight:500;vertical-align:middle;letter-spacing:-.5px}
.logo-sub{font-size:22px;font-weight:300;margin-left:36px;margin-top:-4px;letter-spacing:.5px}
.appointment{right:81px;top:48px;text-align:right;color:#fff;font-family:"Open Sans",sans-serif}
.appointment small{display:block;font-size:12px;font-weight:600}
.appointment strong{display:block;font-size:21px;font-weight:400;line-height:1.1}
.main-nav{left:61px;top:100px;width:890px;height:41px;display:flex;background:var(--nav-bg)}
.main-nav a{flex:1;display:flex;align-items:center;justify-content:center;font-size:14px;font-weight:600;color:#666;text-decoration:none;border-right:1px solid #d4d4d4;background:linear-gradient(#f6f6f6,#e2e2e2)}
.main-nav a.active{background:linear-gradient(#8c1044,#5e0028);color:#fff}
.main-nav a:last-child{border-right:0}
.slider{left:63px;top:141px;width:888px;height:317px;overflow:hidden;background:#ddd}
.slider-photo{left:0;top:0;width:700px;height:317px;background:linear-gradient(90deg,#8a7d6e 0%,#d8d2ca 40%,#bfb4a8 70%,#9a9088 100%)}
.slider svg{position:absolute;left:0;top:0}
.slide-copy{left:613px;top:82px;width:250px;color:#fff}
.slide-copy h2{font-family:"Ubuntu",sans-serif;font-weight:300;font-size:30px;line-height:1}
.slide-copy p{font-size:11px;font-weight:300;line-height:19px;margin-top:12px}
.slide-arrows{left:833px;top:287px;color:#fff;font-size:22px;letter-spacing:4px;font-family:"Ubuntu",sans-serif;font-weight:300}
.content{left:63px;top:458px;width:888px;height:621px;background:#fff}
.welcome{left:81px;top:494px;width:290px}
h3.title{font-family:"Ubuntu",sans-serif;font-weight:400;font-size:22px;color:var(--ink)}
.welcome h4{font-family:"Ubuntu",sans-serif;font-weight:400;font-size:14px;color:var(--green-text);margin:6px 0 6px 3px}
.welcome p{font-size:10.5px;line-height:18.4px;margin:0 0 8px 3px}
.opps{left:396px;top:495px;width:250px}
.opps h3{font-weight:300}
.opp{margin-top:12px}
.opp time{display:block;font-size:12px;color:var(--burgundy)}
.opp b{display:block;font-weight:400;font-size:10.5px;color:#444;margin-top:3px}
.opp p{font-size:9px;font-weight:300;color:var(--muted);line-height:17px}
.services-box{left:680px;top:489px;width:257px;height:205px;border:1px solid #ddd;border-radius:3px;background:#fff;overflow:hidden}
.services-box h3{background:linear-gradient(#8a0c44,#600030);color:#fff;font-family:"Ubuntu",sans-serif;font-weight:400;font-size:19px;height:41px;padding:9px 21px}
.services-box ul{list-style:none;margin:8px 25px 0 15px}
.services-box li{font-size:10.5px;color:#333;padding:6px 0 6px 13px;border-bottom:1px solid #ddd;position:relative;white-space:nowrap}
.services-box li:last-child{border-bottom:0}
.services-box li::before{content:"›";position:absolute;left:2px;top:4px;color:#aaa}
.divider{left:82px;top:734px;width:853px;height:4px;background:#e2e2e2;border-bottom:1px solid #ccc}
.col-sep{top:738px;width:4px;height:309px;background:#e4e4e4}
.col-head{top:762px;font-family:"Open Sans",sans-serif;font-size:19px;color:#555;letter-spacing:.2px}
.pager{top:765px;display:flex;gap:2px}
.pager span{width:19px;height:18px;background:#1d1d1d;color:#e96a1a;font-size:9px;display:flex;align-items:center;justify-content:center}
.col-rule{top:803px;height:1px;background:#ddd}
.svc-list{left:101px;top:818px;width:253px;font-family:"Arimo",sans-serif;font-size:10px;color:#222}
.svc-list p{text-align:justify;line-height:15px;margin-bottom:12px}
.svc-list ul{list-style:none}
.svc-list li{padding-left:20px;position:relative;height:31px}
.svc-list li::before{content:"";position:absolute;left:4px;top:3px;width:8px;height:8px;border-radius:50%;background:#222}
.events{left:383px;top:816px;width:255px}
.event{display:flex;gap:11px;height:81px;border-bottom:1px solid #ddd;margin-bottom:6px}
.event:last-child{border-bottom:0}
.event .thumb{width:59px;height:59px;flex:none;margin-top:2px;background:linear-gradient(135deg,#c9b8a4,#4a4038)}
.event .info{font-family:"Arimo",sans-serif;font-size:9.5px;color:#555;line-height:14.5px}
.event time{display:block;font-size:10.5px;color:var(--green-text);font-weight:700;margin-top:-1px}
.event b{display:block;color:var(--burgundy);font-size:10.5px;margin:3px 0 2px}
.video{left:672px;top:825px;width:251px;height:216px;border:1px solid #ccc}
.video-frame{width:100%;height:202px;background:radial-gradient(circle at 30% 40%,#e8d470 0%,#b89030 14%,#3a2420 40%,#1a1010 100%)}
.play{left:108px;top:84px;width:38px;height:38px;border-radius:50%;background:rgba(200,200,200,.6)}
.play::after{content:"";position:absolute;left:15px;top:11px;border-left:12px solid #fff;border-top:8px solid transparent;border-bottom:8px solid transparent}
.video-bar{left:0;top:202px;width:249px;height:12px;background:#f3f3f3;font-size:7px;font-family:"Arimo",sans-serif;font-weight:700;color:#222;display:flex;align-items:center;gap:6px;padding:0 4px}
.video-bar .track{flex:1;height:3px;background:#bbb}
.footer{left:0;top:1098px;width:1016px;height:102px;background:var(--footer-bg)}
.footer-nav{left:85px;top:1125px;font-family:"Ubuntu Condensed",sans-serif;font-size:14px;color:#333}
.footer-nav span{margin:0 5px;color:#333}
.copyright{left:85px;top:1152px;font-size:10px;color:#999}
.social{top:1120px;width:24px;height:24px;border-radius:50%;background:#555}
</style>
</head>
<body>
<div class="abs vineyard-bg" role="img" aria-label="Soft-focus vineyard rows framing the page"></div>
<div class="abs header-band"></div>
<div class="abs header-photo" role="img" aria-label="Bunch of dark blue grapes on the vine"></div>

<div class="abs logo">
  <span class="logo-mark"></span><span class="logo-name">bluefern</span>
  <div class="logo-sub">Business Services</div>
</div>
<div class="abs appointment"><small>Make an Appointment</small><strong>+91 (44) 5550 1234</strong></div>

<nav class="abs main-nav">
  <a class="active" href="#">HOME</a><a href="#">ABOUT US</a><a href="#">CLIENTS</a><a href="#">SERVICES</a><a href="#">CAREERS</a><a href="#">CONTACT US</a>
</nav>

<section class="abs slider">
  <div class="abs slider-photo" role="img" aria-label="Business team smiling around a meeting table"></div>
  <svg width="888" height="317" viewBox="0 0 888 317">
    <path d="M888 0 H640 C560 60 540 230 680 317 H888 Z" fill="#fff" opacity=".85"/>
    <path d="M888 0 H650 C575 60 560 230 700 317 H888 Z" fill="#7d8a2a"/>
  </svg>
  <div class="abs slide-copy">
    <h2>Provide Software Consulting</h2>
    <p>Suspendisse vulputate aliquam dui. Nulla elementum dui ut augue. Aliquam vehicula mi at mauris Maecenas placerat nisl</p>
  </div>
  <div class="abs slide-arrows">‹ ›</div>
</section>

<div class="abs content"></div>

<section class="abs welcome">
  <h3 class="title">Welcome to Our Website!</h3>
  <h4>Delivering IT Excellence</h4>
  <p>Welcome to Bluefern Business Services, an emerging provider of global IT consulting and software services.</p>
  <p>We are part of the Marlow Goods group, a family run business and the world's largest multi-channel home delivery wine merchant. Ut accumsan ultricies elit. Maecenas at justo id velit placerat molestie. Donec dictum lectus non odio. Cras a ante vitae enim iaculis aliquam.</p>
</section>

<section class="abs opps">
  <h3 class="title">Latest Opportunities</h3>
  <div class="opp"><time>26/11/2013</time><b>Software Developers/Programmer Analysts - AX</b><p>Class aptent taciti sociosqu ad litora torquent per conubia nostra, per inceptos hymenaeos.</p></div>
  <div class="opp"><time>28/11/2013</time><b>Aliquam nec erat at purus cursus</b><p>Proin nulla arcu, nonummy luctus, dictum eget, fermentum et, lorem. Nunc porta convallis pede.</p></div>
</section>

<aside class="abs services-box">
  <h3>Services We Provide</h3>
  <ul>
    <li>Packaged Applications</li>
    <li>Enterprise Application Integration</li>
    <li>Digital Commerce</li>
    <li>Application Development &amp; Maintenance</li>
    <li>Business Software Consulting</li>
  </ul>
</aside>

<div class="abs divider"></div>
<div class="abs col-sep" style="left:367px"></div>
<div class="abs col-sep" style="left:654px"></div>

<h3 class="abs col-head" style="left:101px">SERVICES</h3>
<div class="abs pager" style="left:316px"><span>&lt;</span><span>&gt;</span></div>
<div class="abs col-rule" style="left:101px;width:253px"></div>
<section class="abs svc-list">
  <p>The services we provide enable the businesses we support to efficiently manage key functions, including order management.</p>
  <ul>
    <li>Packaged Applications</li>
    <li>Enterprise Application Integration</li>
    <li>Digital Commerce</li>
    <li>Application Development &amp; Maintenance</li>
    <li>Multiple versions of Corvane Commerce</li>
    <li>Ledgerline AX 2009</li>
  </ul>
</section>

<h3 class="abs col-head" style="left:383px">RECENT EVENTS</h3>
<div class="abs pager" style="left:601px"><span>&lt;</span><span>&gt;</span></div>
<div class="abs col-rule" style="left:383px;width:255px"></div>
<section class="abs events">
  <div class="event"><div class="thumb" role="img" aria-label="Event photo of colleagues talking"></div><div class="info"><time>JAN 07 2014</time><b>Business Services we design</b>Marlow Goods IT landscape. Current plans to strategically transform this landscape</div></div>
  <div class="event"><div class="thumb" role="img" aria-label="Event photo of team members together"></div><div class="info"><time>JAN 07 2014</time><b>Business Services we design</b>Marlow Goods IT landscape. Current plans to strategically transform this landscape</div></div>
  <div class="event"><div class="thumb" role="img" aria-label="Event photo of a team celebration"></div><div class="info"><time>JAN 07 2014</time><b>Business Services we design</b>Marlow Goods IT landscape. Current plans to strategically transform this landscape</div></div>
</section>

<h3 class="abs col-head" style="left:671px">VIDEOS</h3>
<div class="abs pager" style="left:886px"><span>&lt;</span><span>&gt;</span></div>
<div class="abs col-rule" style="left:671px;width:252px"></div>
<div class="abs video">
  <div class="video-frame" role="img" aria-label="Video still of wine glasses and grapes"></div>
  <div class="abs play"></div>
  <div class="abs video-bar"><span>▶</span><span>00:01</span><span class="track"></span><span>100 %</span><span>▣</span><span>◂ıll</span></div>
</div>

<footer class="abs footer"></footer>
<nav class="abs footer-nav">HOME<span>|</span>ABOUT US<span>|</span>CLIENTS<span>|</span>SERVICES<span>|</span>CAREERS<span>|</span>CONTACT US</nav>
<div class="abs copyright">Copyright © 2013 Company Name.&nbsp; All right reserved</div>
<div class="abs social" style="left:844px" aria-label="Social link"></div>
<div class="abs social" style="left:871px" aria-label="Social link"></div>
<div class="abs social" style="left:899px" aria-label="Social link"></div>
</body>
</html>
```